Ward Compass Business Card Design*

We need a business card design for our company Ward Compass. Our company is specialized in providing online consulting services regarding medical institutions, hospitals and doctors. We work with patients worldwide looking to choose between healthcare providers. We have a website you may use as a reference, where we list doctors and clinics worldwide. So we target Medical providers as well as patients worldwide.
Target Market(s)
Medical Providers and patients around the world
Industry/Entity Type
Medical
Contact Information for Business Card
Salwa Kettani
CEO
+90 612 348 2175
info@wardcompass.example
www.wardcompass.example
14 Annakhil 7 H.R.B. Rabat, Morocco
Requirements
Must have
- Company logo/name on one full side, personal info and smaller logo and company name on the other side.
Nice to have
- Smart and elegant design

```html
<!DOCTYPE html>
<html lang="en">
<head>
<meta charset="utf-8">
<title>Ward Compass Business Card</title>
<link href="https://fonts.googleapis.com/css2?family=Nunito+Sans:wght@400;700;800&display=swap" rel="stylesheet">
<style>
  :root {
    --navy: #1a4474;
    --grey: #7b797a;
    --paper: #f3f3f5;
    --white: #ffffff;
    --backdrop: #e7e4df;
  }
  * { margin: 0; padding: 0; box-sizing: border-box; }
  html, body { width: 900px; height: 1200px; overflow: hidden; }
  body {
    background: var(--backdrop);
    font-family: "Nunito Sans", Arial, sans-serif;
    position: relative;
  }
  .card {
    position: absolute;
    left: 70px;
    width: 760px;
    height: 445px;
    overflow: hidden;
    box-shadow: 0 4px 10px rgba(0,0,0,0.25);
  }
  .card-front { top: 140px; background: var(--paper); }
  .card-back { top: 620px; background: var(--navy); }

  .base-band { position: absolute; left: 0; top: 0; width: 100%; height: 100%; }

  .brand {
    position: absolute;
    display: flex;
    align-items: center;
    font-weight: 700;
    letter-spacing: 0.5px;
    text-transform: uppercase;
    white-space: nowrap;
  }
  .brand-dot { border-radius: 50%; flex: none; }
  .card-front .brand { left: 56px; top: 53px; color: var(--navy); font-size: 28px; gap: 16px; }
  .card-front .brand-dot { width: 74px; height: 74px; background: var(--navy); }
  .card-back .brand { left: 0; right: 0; top: 168px; justify-content: center; color: var(--white); font-size: 46px; gap: 24px; }
  .card-back .brand-dot { width: 112px; height: 112px; background: var(--grey); }

  .person { position: absolute; right: 48px; top: 54px; text-align: right; color: var(--navy); }
  .person-name { font-size: 27px; line-height: 1; letter-spacing: 0.3px; }
  .person-name .first { font-weight: 800; }
  .person-name .last { font-weight: 400; }
  .person-role { font-size: 17px; color: var(--grey); margin-top: 4px; }

  .contact { position: absolute; left: 55px; top: 306px; color: var(--white); font-size: 17px; line-height: 23px; }
  .contact-lines { margin-top: 16px; }
  .contact-row { display: flex; align-items: center; gap: 12px; }
  .contact-row svg { width: 15px; height: 15px; flex: none; }

  .website {
    position: absolute; left: 0; right: 0; top: 404px;
    text-align: center; color: var(--white);
    font-size: 17px; letter-spacing: 4px;
  }
</style>
</head>
<body>

<section class="card card-front">
  <svg class="base-band" viewBox="0 0 760 445" preserveAspectRatio="none" aria-hidden="true">
    <path d="M0,270 C200,250 520,280 760,330 L760,445 L0,445 Z" fill="#1a4474"/>
  </svg>

  <div class="brand"><span class="brand-dot"></span>Ward Compass</div>

  <div class="person">
    <p class="person-name"><span class="first">SALWA</span> <span class="last">KETTANI</span></p>
    <p class="person-role">CEO</p>
  </div>

  <div class="contact">
    <p>14 Annakhil 7 H.R.B.<br>Rabat, Morocco</p>
    <div class="contact-lines">
      <p class="contact-row">
        <svg viewBox="0 0 24 24" aria-hidden="true"><path fill="#fff" d="M6.6 10.8a15.1 15.1 0 0 0 6.6 6.6l2.2-2.2c.3-.3.7-.4 1-.2 1.1.4 2.3.6 3.6.6.6 0 1 .4 1 1V20c0 .6-.4 1-1 1A17 17 0 0 1 3 4c0-.6.4-1 1-1h3.5c.6 0 1 .4 1 1 0 1.3.2 2.5.6 3.6.1.3 0 .7-.2 1z"/></svg>
        +90 612 348 2175
      </p>
      <p class="contact-row">
        <svg viewBox="0 0 24 24" aria-hidden="true"><path fill="#fff" d="M2 5h20v14H2z"/><path fill="none" stroke="#1a4474" stroke-width="1.8" d="M2 5l10 8 10-8M2 19l7-7M22 19l-7-7"/></svg>
        info@wardcompass.example
      </p>
    </div>
  </div>
</section>

<section class="card card-back">
  <div class="brand"><span class="brand-dot"></span>Ward Compass</div>
  <p class="website">www.wardcompass.example</p>
</section>

</body>
</html>
```